Business card design for holistic health care clinic

We need a double-sided business card design for our holistic health care clinic that integrates our logo design and also its color scheme. My business is called Valmira. It is an integrative medicine clinic. You have already done the logo for me. Please ensure an elegant and upscale design that is not cluttered, but still has all the necessary information (please see below for details).

Target Market(s)

Wellness, fitness, rehabilitation for educated, well-traveled open-minded clients who are focused on natural, organic, balanced and preventive healthcare and lifestyle.

Industry/Entity Type

Medical

Contact Information for Business Card

Modern, clean.

Number of Pages Required

1 page

Font styles to use
Serif
Sans Serif

Colors

Designer to choose colors to be used in the design.

Requirements
Must have
• Logo on one side, all other information on the other side.
• Other information should include:
• Tobias Wrenfeld - DOE, CPT, LMT
• 4100 East Marrow Drive
• Austin, TX 78119
• 512 555 0148
• 818 555 0192
• info@ValmiraHealth.example
• t.wrenfeld@ValmiraHealth.example
Nice to have
• Darker background on front - but not totally black - shaded/dark gray.

```html
<!DOCTYPE html>
<html lang="en">
<head>
<meta charset="utf-8">
<title>Valmira — Business Card</title>
<link rel="stylesheet" href="https://fonts.googleapis.com/css2?family=Montserrat:wght@400;500;700;800&display=swap">
<style>
  :root {
    --page-bg: #3a3b3e;
    --brand-blue: #1b8fd2;
    --brand-blue-light: #2aa3e4;
    --brand-blue-deep: #16639b;
    --card-dark: #2a2b2f;
    --card-dark-edge: #232427;
    --text-light: #e6e7ea;
    --text-muted: #a9abb1;
    --rule: #6d7077;
  }
  * { box-sizing: border-box; margin: 0; padding: 0; }
  html, body { width: 1200px; height: 960px; overflow: hidden; }
  body {
    background: var(--page-bg);
    font-family: "Montserrat", Arial, sans-serif;
    position: relative;
  }
  .card {
    position: absolute;
    left: 230px;
    width: 740px;
    height: 423px;
    border-radius: 4px;
    overflow: hidden;
    box-shadow: 0 10px 30px rgba(0,0,0,.35);
  }

  /* Logo side */
  .card-logo {
    top: 40px;
    background: linear-gradient(135deg, var(--brand-blue-light), var(--brand-blue));
  }
  .card-logo .brand {
    position: absolute;
    left: 0; right: 0; top: 120px;
    text-align: center;
  }
  .card-logo .brand-name {
    font-weight: 800;
    font-size: 84px;
    letter-spacing: 2px;
    color: #ffffff;
    line-height: 1;
  }
  .card-logo .brand-sub {
    margin-top: 8px;
    font-weight: 700;
    font-size: 24px;
    color: var(--brand-blue-deep);
  }
  .card-logo .tagline {
    position: absolute;
    left: 250px; top: 312px;
    display: flex; align-items: center; gap: 12px;
    color: #ffffff;
    font-size: 17px;
    font-weight: 500;
  }
  .card-logo .tagline-rule {
    width: 150px; height: 1px; background: rgba(255,255,255,.85);
  }

  /* Info side */
  .card-info {
    top: 497px;
    background: linear-gradient(160deg, var(--card-dark), var(--card-dark-edge));
  }
  .card-info .decor {
    position: absolute;
    left: -60px; top: -40px;
    width: 420px; height: 260px;
    background: radial-gradient(ellipse at 40% 50%, rgba(27,143,210,.22), rgba(27,143,210,0) 70%);
  }
  .card-info .holder {
    position: absolute;
    left: 40px; top: 52px;
    color: var(--brand-blue);
    font-weight: 700;
    font-size: 24px;
    letter-spacing: .5px;
  }
  .card-info .holder .credentials {
    font-size: 13px;
    color: var(--text-muted);
    font-weight: 500;
    letter-spacing: 0;
  }
  .card-info .name-rule {
    position: absolute;
    left: 40px; top: 92px;
    width: 660px; height: 1px;
    background: var(--rule);
  }
  .card-info .brand {
    position: absolute;
    right: 40px; top: 112px;
    text-align: left;
    color: var(--brand-blue);
  }
  .card-info .brand-name {
    font-weight: 800;
    font-size: 62px;
    letter-spacing: 1px;
    line-height: 1;
  }
  .card-info .brand-sub {
    margin-top: 4px;
    font-weight: 700;
    font-size: 18px;
    padding-bottom: 8px;
    border-bottom: 1px solid var(--rule);
  }
  .card-info .contact {
    position: absolute;
    left: 40px; top: 210px;
    list-style: none;
    color: var(--text-light);
    font-size: 19px;
    line-height: 28px;
  }
  .card-info .contact li { display: flex; align-items: center; gap: 10px; }
  .card-info .contact svg { width: 15px; height: 15px; fill: var(--brand-blue); }
  .card-info .contact .email { padding-left: 25px; }
  .card-info .address {
    position: absolute;
    right: 40px; top: 292px;
    text-align: right;
    font-style: normal;
    color: var(--text-light);
    font-size: 20px;
    line-height: 28px;
  }
</style>
</head>
<body>
  <section class="card card-logo">
    <div class="brand">
      <div class="brand-name">VALMIRA</div>
      <div class="brand-sub">Integrative Holistic Medicine</div>
    </div>
    <div class="tagline">helping the body help itself <span class="tagline-rule"></span></div>
  </section>

  <section class="card card-info">
    <div class="decor" role="img" aria-label="Faint brand decoration area"></div>
    <div class="holder">TOBIAS WRENFELD <span class="credentials">- DOE, CPT, LMT</span></div>
    <div class="name-rule"></div>
    <div class="brand">
      <div class="brand-name">VALMIRA</div>
      <div class="brand-sub">Integrative Holistic Medicine</div>
    </div>
    <ul class="contact">
      <li>
        <svg viewBox="0 0 16 16" aria-hidden="true"><path d="M3 1l3 3-1.5 2a9 9 0 0 0 5.5 5.5L12 10l3 3-2 2C7 15 1 9 1 3z"/></svg>
        512 555 0148
      </li>
      <li>
        <svg viewBox="0 0 16 16" aria-hidden="true"><path d="M4 0h8a1 1 0 0 1 1 1v14a1 1 0 0 1-1 1H4a1 1 0 0 1-1-1V1a1 1 0 0 1 1-1zm1 2v10h6V2zm3 11a1 1 0 1 0 0 2 1 1 0 0 0 0-2z"/></svg>
        818 555 0192
      </li>
      <li>
        <svg viewBox="0 0 16 16" aria-hidden="true"><path d="M1 3h14v10H1zm1 1.5V12h12V4.5L8 9z"/></svg>
        info@ValmiraHealth.example
      </li>
      <li class="email">t.wrenfeld@ValmiraHealth.example</li>
    </ul>
    <address class="address">
      4100 East Marrow Drive<br>
      Austin, TX 78119<br>
      www.ValmiraHealth.example
    </address>
  </section>
</body>
</html>
```